A unique communication angle to crowdfunding

Looking for a fresh redesign of a crowd funding website that deals in real estate. I already have the content, but am looking to take the design to the next level.

Existing real estate crowd funding sites focus on the real estate. I want to explore communication angle that:
- puts the investor in the centre of the communication: "become a baron"
- highlights the international nature (international properties, international investors)

There's also quite a lot of copy on the site, as we need to explain the service in quite a bit of detail. There's room to reduce the copy and replace with graphics. Could also consider clicking to see different text (see our difference section in http://galleonfairs.com)

The backend of the platform is already being worked on by a specialist crowd funding service provider.

In total there are 5 pages to be designed.

The homepage is really important. Right now it looks quite dated. It doesn't have a great layout. Note there is no mobile version of the website, so the pages need to be seen well on mobile devices. When looking at the brief, refer to the following links too:

current website:
http://pennyduke.com

some revisions made so far:
http://preview.stakeharbor.com/7K3LQ9

Attached are logo files and another file which contained copy for the pages. No need to rework the logo.

Please make sure to use the same copy in the brief on the webpages, to ensure the layouts work. Designers are free to propose images they feel work on the pages.

I would like to see if rather than tweaking the pages, it's possible to come up with a better design concept. If the 5 pages are accepted, there's a chance I'll request an additional 4 pages.
Updates

Please note the font used in the logo is called "harabara" in case you decide to use it in any of the titles, etc.

Please note there is one additional page for which we would like to review designs. Note the page would be a template to be used on all future real estate detail pages. Here is an example of the current design for reference:

http://pennyduke.com/projects/view/14

In total there are 5 page designs required, (homepage + 4)

Thank you

FYI -

Just a quick note to give information from similar UK real estate crowdfunding sites:
http://www.housewalrus.co.uk
http://tiderock.co.uk
https://www.fundquarry.com

Of the above, only tiderock has a nice clean looking landing page. Information is clear and well laid out.

Hi all, just uploaded a new file in the brief. Contains some comments and a website reference. I thought it may help to explain how we could convey international aspect as well as how we could convey images in a more modern way. This is an option you can consider, but its entirely up to you how how answer the brief. Thanks!

Reason: As requested by some designers needing more time to complete their work. Continue to share your work in progress and receive timely feedback before the deadline.

We would like to let you know that we have just shortlisted the best designs. Together with that, we have also passed some detailed feedback to all designers who weren't shortlisted. If we didn't contact you, please let us know. If you haven't submitted a design or are working on revisions, please note these will no longer be taken into account now. We hope you understand that we need to close the project today. Thank you all once again for your great work and design concepts. Here's hoping we meet again on a future design brief. Cheers, pennyduke team.

Target Market(s)

At the moment, only rich are able to buy real estate. With this service, anyone can become a landlord. Target buyers:

Young professionals, looking to diversify from stock market and lower risk
People nearing retirement, looking for stable rental incomes
Retirees - looking to supplement pensions with possibility of capital gains
Parents - looking for a way to save long term for their children (instead of low interest paying bank accounts)

Industry/Entity Type

Communication

Font styles to use
Sans Serif
Other font styles liked:
• harabara

Colors
add136
f5f9eb
959595
000000

Requirements
Must have
• Overall, the site must convey "whoever you are, you too can become a landlord", and that you don't need to be wealthy to invest in real estate. See

Communication should put the investor (or the baron) at the centre. The investor can be any of those described in the target market.

Show the aspirational side of property ownership.

In addition to the investor/baron character, the second main theme is international. No other real estate crowdfunding website highlights this.
Nice to have
• Banner could show different consumer types, to illustrate that the service can appeal to many different profiles. Refer to attached file "home page reference - plainasbread.com" as an example of how this could be done.

Aim to show the international side of the service. Properties around the world, investors around the world.

```html
<!DOCTYPE html>
<html lang="en">
<head>
<meta charset="utf-8">
<title>pennyduke — Social real estate investment</title>
<link href="https://fonts.googleapis.com/css2?family=Nunito:wght@700;800&family=Open+Sans:wght@400;600;700&display=swap" rel="stylesheet">
<style>
:root{
  --green:#8cc63f;
  --green-dark:#6fa82a;
  --green-light:#f5f9eb;
  --ink:#333333;
  --grey:#959595;
  --grey-light:#f2f2f2;
  --line:#e1e1e1;
  --darker:#3a3a3a;
  --white:#ffffff;
}
*{box-sizing:border-box;margin:0;padding:0}
html,body{width:1200px;height:3000px;overflow:hidden}
body{font-family:"Open Sans",Arial,sans-serif;color:var(--ink);background:var(--white);position:relative}
.abs{position:absolute}
.heading{font-family:"Nunito",Arial,sans-serif;font-weight:800;color:var(--green)}

/* header */
.site-header{position:absolute;left:0;top:0;width:1200px;height:96px;background:var(--white)}
.brand{left:154px;top:24px;display:flex;align-items:center;gap:10px}
.brand-mark{width:32px;height:32px;border-radius:50%;background:var(--green)}
.brand-name{font-weight:700;font-size:27px;color:var(--green)}
.follow{left:618px;top:22px;display:flex;align-items:center;gap:8px;font-size:13px;color:var(--ink)}
.social-box{width:36px;height:26px;background:var(--green)}
.social-box.alt{background:#f2f2f2;border:1px solid #e2e2e2}
.search{left:812px;top:22px;width:242px;height:28px;display:flex}
.search-field{flex:1;background:#eeeeee;font-size:11px;color:var(--grey);padding:7px 10px}
.search-btn{width:36px;background:#5a5a5a;display:flex;align-items:center;justify-content:center}
.main-nav{left:460px;top:66px;display:flex;font-size:11px;font-weight:600}
.main-nav span{padding:4px 11px 8px;color:#555;white-space:nowrap}
.main-nav .active{color:var(--ink);border-bottom:3px solid #555;font-weight:700}

/* hero */
.hero{position:absolute;left:0;top:96px;width:1200px;height:394px;overflow:hidden}
.hero-visual{position:absolute;inset:0;
  background:
    radial-gradient(ellipse 260px 170px at 300px 150px,rgba(214,206,190,.95) 0%,rgba(200,190,170,.7) 55%,rgba(200,190,170,0) 100%),
    radial-gradient(ellipse 180px 70px at 280px 40px,rgba(70,62,58,.9) 0%,rgba(70,62,58,0) 100%),
    radial-gradient(ellipse 360px 180px at 760px 170px,rgba(118,176,40,.95) 0%,rgba(118,176,40,.6) 60%,rgba(118,176,40,0) 100%),
    radial-gradient(ellipse 120px 110px at 880px 330px,rgba(188,190,170,.95) 0%,rgba(190,170,110,.5) 55%,rgba(255,255,255,0) 100%),
    linear-gradient(180deg,#5b9fe0 0%,#9fcbee 30%,#a9d46a 55%,#8dc53c 68%,#f4f4f4 86%,#ffffff 100%)}
.hero-shadow{left:160px;top:388px;width:880px;height:8px;border-radius:50%;background:radial-gradient(ellipse at center,rgba(0,0,0,.25),rgba(0,0,0,0) 70%)}
.hero-caption{left:176px;top:214px;width:504px;height:84px;background:rgba(40,40,40,.88);padding:12px 20px}
.hero-caption h1{font-family:"Nunito",Arial,sans-serif;font-weight:800;color:var(--green);font-size:24px;line-height:1.1}
.hero-caption p{color:var(--green);font-size:13px;margin-top:12px}
.hero-arrow{top:172px;width:40px;height:40px;border-radius:50%;background:rgba(40,40,40,.85);border:2px solid var(--green);display:flex;align-items:center;justify-content:center}
.hero-dots{left:130px;top:370px;display:flex;gap:6px}
.hero-dots i{width:10px;height:10px;border-radius:50%;background:#555;display:block}
.hero-dots i:first-child{background:var(--green)}

/* intro */
.intro{position:absolute;left:0;top:490px;width:1200px;height:300px;text-align:center}
.intro h2{position:absolute;top:40px;width:100%;font-size:29px}
.intro .rule{position:absolute;left:400px;top:88px;width:400px;height:2px;background:var(--line)}
.intro-copy{position:absolute;top:104px;left:200px;width:800px;font-size:13.5px;line-height:24px;color:#555}
.intro-copy p{margin-bottom:22px}
.hl{color:var(--green);font-weight:600}

/* call to action band */
.cta-band{position:absolute;left:0;top:790px;width:1200px;height:302px;background:var(--grey-light)}
.cta{position:absolute;top:48px;width:368px}
.cta-card{height:146px;background:var(--white);border:1px solid var(--line);display:flex;padding:26px 16px;gap:18px}
.cta-icon{width:78px;height:78px;border-radius:50%;background:#4a4a4a;flex:none;display:flex;align-items:center;justify-content:center}
.cta-card h3{font-size:21px;margin-bottom:6px}
.cta-card p{font-size:12.5px;line-height:22px;color:#555}
.cta-btn{margin-top:12px;height:44px;background:var(--green);border-bottom:3px solid var(--green-dark);color:var(--white);font-family:"Nunito",Arial,sans-serif;font-weight:800;font-size:20px;display:flex;align-items:center;justify-content:center;box-shadow:0 3px 5px rgba(0,0,0,.15)}

/* featured projects */
.projects{position:absolute;left:0;top:1092px;width:1200px;height:622px;text-align:center}
.projects h2{position:absolute;top:22px;width:100%;font-size:22px}
.projects .lead{position:absolute;top:60px;left:310px;width:580px;font-size:13px;line-height:24px;color:#555}
.project{position:absolute;top:144px;width:290px;height:416px;background:var(--white);border:1px solid var(--line);text-align:left}
.project.first{box-shadow:0 3px 8px rgba(0,0,0,.2)}
.project-photo{position:relative;height:206px;
  background:
    radial-gradient(ellipse 120px 46px at 150px 108px,rgba(168,88,58,.95) 0%,rgba(168,88,58,.6) 60%,rgba(168,88,58,0) 100%),
    radial-gradient(ellipse 130px 24px at 150px 66px,rgba(70,66,66,.85) 0%,rgba(70,66,66,0) 100%),
    linear-gradient(180deg,#3f7fd2 0%,#86b3e6 32%,#b7d0ea 44%,#b06b46 56%,#9a5e3e 72%,#c8c2b8 82%,#6e9c3c 100%)}
.project-photo.b{
  background:
    radial-gradient(ellipse 120px 48px at 150px 110px,rgba(200,188,170,.95) 0%,rgba(160,120,96,.6) 60%,rgba(160,120,96,0) 100%),
    radial-gradient(ellipse 130px 26px at 150px 66px,rgba(80,72,70,.85) 0%,rgba(80,72,70,0) 100%),
    linear-gradient(180deg,#4f8fda 0%,#9cc2ea 34%,#c9d8e6 46%,#a27a5c 58%,#d8d2c6 76%,#cfc9bd 86%,#7ea64a 100%)}
.project-photo.c{
  background:
    radial-gradient(ellipse 90px 90px at 250px 70px,rgba(64,112,44,.95) 0%,rgba(64,112,44,0) 100%),
    radial-gradient(ellipse 120px 40px at 130px 120px,rgba(238,228,210,.95) 0%,rgba(238,228,210,0) 100%),
    radial-gradient(ellipse 110px 22px at 130px 92px,rgba(196,98,58,.9) 0%,rgba(196,98,58,0) 100%),
    linear-gradient(180deg,#3a7fd6 0%,#8ab8e8 40%,#e0d6c0 60%,#6d9b45 84%,#4f7f38 100%)}
.price-tag{position:absolute;left:0;top:0;background:var(--green);color:var(--white);font-size:10px;font-weight:700;padding:6px 8px}
.new-tag{position:absolute;left:0;top:34px;background:#555;color:var(--green);font-size:9px;padding:3px 8px}
.project h4{font-size:14.5px;font-weight:600;color:var(--green);margin:18px 18px 6px}
.project p{font-size:11.5px;line-height:20px;color:#555;margin:0 18px}
.funded{margin:16px 12px 0;font-size:12.5px;font-weight:700;color:var(--ink)}
.bar{margin:4px 12px 0;height:20px;border:1px solid #cfcfcf;border-radius:3px;background:#f6f6f6;position:relative;font-size:11px;text-align:center;line-height:18px;color:var(--ink)}
.bar i{position:absolute;left:0;top:0;bottom:0;background:var(--green);border-radius:2px}
.bar span{position:relative}
.details{text-align:center;font-size:12.5px;font-weight:600;color:#666;margin-top:8px}
.first .details{color:var(--green)}

/* community */
.community{position:absolute;left:0;top:1714px;width:1200px;height:422px;text-align:center;overflow:hidden;
  background:
    radial-gradient(ellipse 700px 120px at 600px 420px,rgba(70,70,70,.9) 0%,rgba(70,70,70,0) 100%),
    linear-gradient(180deg,#4a4a4a 0%,#3c3c3c 40%,#242424 70%,#1c1c1c 100%)}
.community-scene{position:absolute;left:0;right:0;bottom:0;height:200px;
  background:linear-gradient(180deg,rgba(110,110,110,0) 0%,rgba(110,110,110,.25) 50%,rgba(20,20,20,.5) 100%)}
.community h2{position:absolute;top:52px;width:100%;font-size:21px}
.community .lead{position:absolute;top:90px;left:300px;width:600px;font-size:14px;line-height:24px;color:#7c7c7c}
.stat{position:absolute;top:196px;width:260px}
.stat-art{height:124px;background:radial-gradient(ellipse 130px 60px at center,rgba(150,150,150,.32) 0%,rgba(150,150,150,0) 100%)}
.stat b{position:absolute;top:36px;left:0;width:100%;font-family:"Nunito",Arial,sans-serif;font-weight:800;color:var(--green);font-size:20px;line-height:24px}
.stat p{margin-top:10px;font-size:14px;line-height:24px;color:#d8d8d8}

/* press */
.press{position:absolute;left:144px;top:2196px;width:910px;height:194px;border:1px solid var(--line)}
.press-tab{position:absolute;left:378px;top:-18px;width:176px;height:38px;background:var(--green);color:var(--white);font-weight:600;font-size:15px;display:flex;align-items:center;justify-content:center}
.badge{position:absolute;height:22px;background:#6e6e6e;border-radius:3px}
.badge.light{background:#bdbdbd}
.badge.round{border-radius:50%}

/* skyline and footer */
.skyline{position:absolute;left:0;top:2400px;width:1200px;height:140px;
  background:
    radial-gradient(ellipse 40px 120px at 380px 140px,rgba(150,150,150,.95) 0%,rgba(150,150,150,0) 100%),
    radial-gradient(ellipse 30px 110px at 850px 140px,rgba(150,150,150,.95) 0%,rgba(150,150,150,0) 100%),
    linear-gradient(180deg,#ffffff 0%,#ffffff 20%,#cfcfcf 50%,#a5a5a5 78%,#939393 100%)}
.footer-bar{position:absolute;left:0;top:2540px;width:1200px;height:64px;background:var(--darker);display:flex;align-items:center;justify-content:space-between;padding:0 144px}
.footer-follow{display:flex;align-items:center;gap:12px;color:var(--green);font-weight:600;font-size:16px}
.footer-follow i{width:34px;height:34px;border:2px solid var(--green);display:block}
.copyright{color:var(--green);font-size:12px}
.legal{position:absolute;left:144px;top:2624px;width:910px;font-size:12px;line-height:20px;color:#555}
.legal p{margin-bottom:20px}
.legal .intro-line{width:560px}
.group-name{position:absolute;left:700px;top:2px;font-weight:700;font-size:26px;color:#444;line-height:34px;white-space:nowrap}
</style>
</head>
<body>

<header class="site-header">
  <div class="abs brand"><span class="brand-mark"></span><span class="brand-name">pennyduke</span></div>
  <div class="abs follow">Follow us on <span class="social-box"></span><span class="social-box alt"></span></div>
  <div class="abs search">
    <div class="search-field">Search...</div>
    <div class="search-btn">
      <svg width="16" height="16" viewBox="0 0 16 16" aria-hidden="true"><circle cx="6.5" cy="6.5" r="4.5" fill="none" stroke="#fff" stroke-width="2"/><line x1="10" y1="10" x2="14.5" y2="14.5" stroke="#fff" stroke-width="2"/></svg>
    </div>
  </div>
  <nav class="abs main-nav">
    <span class="active">HOME</span><span>SIGN IN</span><span>HOW IT WORKS</span><span>DISCOVER A PROJECT</span><span>THE BARON BLOG</span><span>FIND OUT MORE</span>
  </nav>
</header>

<section class="hero">
  <div class="hero-visual" role="img" aria-label="Stone family house under a blue sky beside green trees, with a small model house and stacks of coins"></div>
  <div class="abs hero-arrow" style="left:94px">
    <svg width="14" height="14" viewBox="0 0 14 14" aria-hidden="true"><path d="M9 2 L4 7 L9 12" fill="none" stroke="#8cc63f" stroke-width="2.5"/></svg>
  </div>
  <div class="abs hero-arrow" style="left:1064px">
    <svg width="14" height="14" viewBox="0 0 14 14" aria-hidden="true"><path d="M5 2 L10 7 L5 12" fill="none" stroke="#8cc63f" stroke-width="2.5"/></svg>
  </div>
  <div class="abs hero-caption">
    <h1>One property at a time</h1>
    <p>Invest from 1% in a property. Diversify across cities and properties.</p>
  </div>
  <div class="abs hero-dots"><i></i><i></i><i></i><i></i></div>
</section>
<div class="abs hero-shadow"></div>

<section class="intro">
  <h2 class="heading">Social real estate investment</h2>
  <div class="rule"></div>
  <div class="intro-copy">
    <p>By harnessing the power of crowds, it's possible to become a landlord in locations around the world. Forget the burden of financing <span class="hl">100%</span> of the purchase.</p>
    <p>Leave the day to day management of your property portfolio to us.</p>
    <p>Start with <span class="hl">1%</span> in a project and plan your steps to becoming a true baron</p>
  </div>
</section>

<section class="cta-band">
  <div class="cta" style="left:202px">
    <div class="cta-card">
      <div class="cta-icon">
        <svg width="40" height="40" viewBox="0 0 40 40" aria-hidden="true"><rect x="6" y="14" width="10" height="22" fill="#8cc63f"/><rect x="18" y="6" width="10" height="30" fill="#8cc63f"/><rect x="30" y="18" width="6" height="18" fill="#8cc63f"/></svg>
      </div>
      <div>
        <h3 class="heading">Find properties</h3>
        <p>Sign up to browse the portfolio. Your journey to becoming a real estate baron starts here.</p>
      </div>
    </div>
    <div class="cta-btn">Become a member</div>
  </div>
  <div class="cta" style="left:630px">
    <div class="cta-card">
      <div class="cta-icon">
        <svg width="40" height="40" viewBox="0 0 40 40" aria-hidden="true"><circle cx="20" cy="10" r="5" fill="#8cc63f"/><rect x="15" y="17" width="10" height="19" rx="3" fill="#8cc63f"/><circle cx="8" cy="14" r="4" fill="#8cc63f"/><rect x="4" y="20" width="8" height="14" rx="3" fill="#8cc63f"/><circle cx="32" cy="14" r="4" fill="#8cc63f"/><rect x="28" y="20" width="8" height="14" rx="3" fill="#8cc63f"/></svg>
      </div>
      <div>
        <h3 class="heading">Find Buyers</h3>
        <p>Submit a property or development and raise funds from our real estate barons.</p>
      </div>
    </div>
    <div class="cta-btn">Submit a property</div>
  </div>
</section>

<section class="projects">
  <h2 class="heading">Featured Projects</h2>
  <p class="lead">Brief details of new and popular projects. To view full listings, you will be required to sign up and <span class="hl">become a member.</span></p>

  <article class="project first" style="left:144px">
    <div class="project-photo" role="img" aria-label="Red brick family house with double garage"><span class="price-tag">From GBP 3,600</span><span class="new-tag">New Launch</span></div>
    <h4>14 Harbour Row LONDON E1</h4>
    <p>Lorem Ipsum is simply dummy text of the printing and typesetting industry. Lorem Ipsum has been the industry's</p>
    <div class="funded">Funded</div>
    <div class="bar"><i style="width:50%"></i><span>50%</span></div>
    <div class="details">See Project Details</div>
  </article>

  <article class="project" style="left:456px">
    <div class="project-photo b" role="img" aria-label="Two storey suburban house with white garage door"><span class="price-tag">From GBP 3,600</span><span class="new-tag">New Launch</span></div>
    <h4>14 Harbour Row LONDON E1</h4>
    <p>Lorem Ipsum is simply dummy text of the printing and typesetting industry. Lorem Ipsum has been the industry's</p>
    <div class="funded">Funded</div>
    <div class="bar"><i style="width:75%"></i><span>75%</span></div>
    <div class="details">See Project Details</div>
  </article>

  <article class="project" style="left:766px">
    <div class="project-photo c" role="img" aria-label="Mediterranean villa with terracotta roof among palm trees"><span class="price-tag">From GBP 3,600</span><span class="new-tag">New Launch</span></div>
    <h4>14 Harbour Row LONDON E1</h4>
    <p>Lorem Ipsum is simply dummy text of the printing and typesetting industry. Lorem Ipsum has been the industry's</p>
    <div class="funded">Funded</div>
    <div class="bar"><i style="width:40%"></i><span>40%</span></div>
    <div class="details">See Project Details</div>
  </article>
</section>

<section class="community">
  <div class="community-scene" role="img" aria-label="Dim black and white city skyline seen from above"></div>
  <h2 class="heading">Be Part of a Growing International Community</h2>
  <p class="lead">Gain access to new projects in world class cities and join our growing community of international landlords</p>

  <div class="stat" style="left:140px">
    <div class="stat-art" role="img" aria-label="Faint world map with location pins"></div>
    <b>3,200 barons<br>in 6 countries</b>
    <p>A community of international<br>property barons.</p>
  </div>
  <div class="stat" style="left:470px">
    <div class="stat-art" role="img" aria-label="Faint group of investor silhouettes"></div>
    <b style="top:50px">USD$ 16.2 million</b>
    <p>Collective buying power of<br>the pennyduke community</p>
  </div>
  <div class="stat" style="left:780px">
    <div class="stat-art" role="img" aria-label="Faint world map with location pins"></div>
    <b>64 proposals in 6<br>countries</b>
    <p>Attractive real estate from<br>around the world</p>
  </div>
</section>

<section class="press" aria-label="Featured In">
  <div class="press-tab">Featured In</div>
  <div class="badge" style="left:36px;top:64px;width:112px"></div>
  <div class="badge" style="left:178px;top:64px;width:152px"></div>
  <div class="badge" style="left:366px;top:62px;width:112px;height:26px"></div>
  <div class="badge" style="left:536px;top:64px;width:276px"></div>
  <div class="badge light" style="left:826px;top:66px;width:48px;height:18px"></div>
  <div class="badge round" style="left:164px;top:124px;width:36px;height:36px;background:#9a9a9a"></div>
  <div class="badge" style="left:252px;top:132px;width:128px;height:18px"></div>
  <div class="badge" style="left:414px;top:124px;width:40px;height:36px"></div>
  <div class="badge" style="left:494px;top:120px;width:72px;height:44px"></div>
  <div class="badge light round" style="left:592px;top:126px;width:30px;height:30px"></div>
  <div class="badge light" style="left:630px;top:132px;width:102px;height:18px"></div>
</section>

<div class="skyline" role="img" aria-label="Grey silhouette of world city landmarks"></div>

<footer>
  <div class="footer-bar">
    <div class="footer-follow">Follow us on <i></i><i></i></div>
    <div class="copyright">© pennyduke 2014</div>
  </div>
  <div class="legal">
    <div class="group-name">Sprout Ventures</div>
    <p class="intro-line"><span class="hl">Penny Duke</span> is part of the Sprout Ventures Group. The Sprout Ventures Group is a worldwide pioneer and leader in the crowd investing, peer to peer and online investment market.</p>
    <p>By accessing this site and any pages thereof, you agree to be bound by the terms and conditions. This website is only suitable, intended and available for professional or sophisticated, or similar investors in other jurisdictions, or those who are members of pennyduke community and familiar with, and willing to, accept the risks associated with private participation. Pennyduke does not endorse any of the projects that appear on this website, nor does it make any recommendations regarding the appropriateness of particular opportunities for any participant. Each potential participant must review and evaluate the projects in his or her own discretion and determine the suitability of participating.</p>
    <p>This website (the "Site") is in every respect unaffiliated with any site to which it links or to any company or entity (and connected projects, investment opportunity or similar) featured on this Site, and is not meant as an endorsement of any of those companies or entities ("third parties"). Furthermore and for the avoidance of doubt, Pennyduke Limited is in no way affiliated with any third parties featured or referenced on this Site. There is no commercial relationship between Pennyduke Limited and such third parties, nor an agency arrangement or similar. If you believe your Content (including third party content) as each such term is defined in our Terms of Service has been reproduced on the Site without permission, please refer to our Terms of Service for information on how to request its removal from the Site.</p>
  </div>
</footer>

</body>
</html>
```